Business Card - connecting 2 souls and beggining the journey of self discovery

Logo on the front
with tag line

On the back list of services and contact details

Seminars
workshops
Coaching
podcasts

Darren Whitlow
Health & Wellbeing Life Coach
0491 372 615
darren@brightcoreliving.example
brightcoreliving.example

Industry/Entity Type

Life Coaching

Contact Information for Business Card

I like the use of colour from the logo to be used. I'm not a fan of white.

Requirements
Must have
• My tagline: The journey home starts with you
Nice to have
• Use of colour that is in the Brightcore Living

```html
<!DOCTYPE html>
<html lang="en">
<head>
<meta charset="utf-8">
<title>Darren Whitlow – Business Card</title>
<link rel="stylesheet" href="https://fonts.googleapis.com/css2?family=Quicksand:wght@400;500;600;700&display=swap">
<style>
  :root {
    --charcoal: #474749;
    --paper: #ffffff;
    --stage: #e6e6e6;
    --green-light: #95c94b;
    --green-mid: #74aa31;
    --green-dark: #4f8021;
    --green-accent: #8cc63f;
    --ink-grey: #6d6e71;
    --wedge-grey: #6a6a6d;
  }
  * { margin: 0; padding: 0; box-sizing: border-box; }
  html, body { width: 1200px; height: 1200px; overflow: hidden; }
  body {
    background: var(--stage);
    font-family: "Quicksand", sans-serif;
    position: relative;
  }
  .card {
    position: absolute;
    left: 120px;
    width: 960px;
    height: 549px;
    overflow: hidden;
    box-shadow: 0 6px 18px rgba(0,0,0,0.18);
  }
  .card--back { top: 36px; }
  .card--front { top: 615px; background: var(--paper); }
  .card__shapes { position: absolute; inset: 0; width: 100%; height: 100%; }

  .identity { position: absolute; left: 45px; top: 72px; }
  .identity__name {
    font-size: 42px; font-weight: 700; color: #fff; letter-spacing: -0.3px; line-height: 1;
  }
  .identity__name .surname { color: var(--green-accent); }
  .identity__role {
    margin-top: 6px; font-size: 23px; font-weight: 500; color: #e4e4e4;
  }

  .contacts { position: absolute; left: 41px; top: 226px; list-style: none; }
  .contacts li {
    display: flex; align-items: center; height: 40px; margin-bottom: 18px;
    font-size: 21px; font-weight: 700; color: #fff;
  }
  .contacts svg { width: 40px; height: 40px; margin-right: 21px; flex: none; }

  .brand { position: absolute; display: flex; flex-direction: column; align-items: center; }
  .brand__dot { border-radius: 50%; background: var(--green-accent); }
  .brand__name { font-weight: 700; color: var(--green-mid); margin-top: 8px; }
  .brand--back { left: 595px; top: 70px; width: 290px; }
  .brand--back .brand__dot { width: 46px; height: 46px; }
  .brand--back .brand__name { font-size: 26px; }
  .brand--front { left: 300px; top: 110px; width: 360px; }
  .brand--front .brand__dot { width: 60px; height: 60px; }
  .brand--front .brand__name { font-size: 34px; }

  .tagline {
    position: absolute; font-weight: 600; color: var(--ink-grey); letter-spacing: -0.3px;
    white-space: nowrap; text-align: center;
  }
  .tagline--back { left: 530px; width: 415px; top: 222px; font-size: 24px; }
  .tagline--front { left: 0; width: 960px; top: 305px; font-size: 43px; }

  .services {
    position: absolute; left: 553px; top: 314px; width: 380px;
    display: grid; grid-template-columns: 205px 175px; row-gap: 26px;
    list-style: none;
  }
  .services li {
    font-size: 29px; font-weight: 500; color: var(--ink-grey); display: flex; align-items: center; line-height: 1.2;
  }
  .services li::before {
    content: ""; width: 8px; height: 8px; border-radius: 50%;
    background: var(--green-accent); margin-right: 9px; flex: none;
  }
</style>
</head>
<body>

  <section class="card card--back" aria-label="Card back with contact details and services">
    <svg class="card__shapes" viewBox="0 0 960 549" preserveAspectRatio="none" aria-hidden="true">
      <rect width="960" height="549" fill="var(--charcoal)"/>
      <polygon points="575,0 960,0 960,477 451,477" fill="var(--paper)"/>
      <polygon points="300,477 420,477 500,549 390,549" fill="var(--green-dark)"/>
      <polygon points="420,477 560,477 640,549 500,549" fill="var(--green-mid)"/>
      <polygon points="560,477 960,477 960,549 640,549" fill="var(--green-light)"/>
    </svg>

    <div class="identity">
      <h1 class="identity__name">Darren <span class="surname">Whitlow</span></h1>
      <p class="identity__role">Health &amp; Wellbeing Life Coach</p>
    </div>

    <ul class="contacts">
      <li>
        <svg viewBox="0 0 40 40" aria-hidden="true">
          <circle cx="20" cy="20" r="20" fill="var(--green-accent)"/>
          <path d="M14 11c1-1 2-1 3 0l2 3c.6 1 .4 2-.4 2.6l-1.2 1c1 2.2 2.8 4 5 5l1-1.2c.6-.8 1.6-1 2.6-.4l3 2c1 1 1 2 0 3l-1.5 1.5c-1.5 1.5-5 .5-9-3.5s-5-7.5-3.5-9z" fill="#fff"/>
        </svg>
        0491 372 615
      </li>
      <li>
        <svg viewBox="0 0 40 40" aria-hidden="true">
          <circle cx="20" cy="20" r="20" fill="var(--green-accent)"/>
          <rect x="10" y="13" width="20" height="14" rx="1.5" fill="none" stroke="#fff" stroke-width="2"/>
          <path d="M10.5 14l9.5 7 9.5-7" fill="none" stroke="#fff" stroke-width="2"/>
        </svg>
        darren@brightcoreliving.example
      </li>
      <li>
        <svg viewBox="0 0 40 40" aria-hidden="true">
          <circle cx="20" cy="20" r="20" fill="var(--green-accent)"/>
          <circle cx="20" cy="20" r="10" fill="none" stroke="#fff" stroke-width="2"/>
          <ellipse cx="20" cy="20" rx="4.5" ry="10" fill="none" stroke="#fff" stroke-width="1.8"/>
          <path d="M10 20h20" stroke="#fff" stroke-width="1.8"/>
        </svg>
        www.brightcoreliving.example
      </li>
    </ul>

    <div class="brand brand--back">
      <span class="brand__dot"></span>
      <span class="brand__name">Brightcore Living</span>
    </div>

    <p class="tagline tagline--back">The journey home starts with you</p>

    <ul class="services">
      <li>Seminars</li>
      <li>Coaching</li>
      <li>Workshops</li>
      <li>Podcasts</li>
    </ul>
  </section>

  <section class="card card--front" aria-label="Card front with brand and tagline">
    <svg class="card__shapes" viewBox="0 0 960 549" preserveAspectRatio="none" aria-hidden="true">
      <rect x="0" y="493" width="960" height="56" fill="var(--green-light)"/>
      <polygon points="560,493 640,493 560,549 470,549" fill="var(--green-mid)"/>
      <polygon points="640,493 697,493 599,549 560,549" fill="var(--green-dark)"/>
      <polygon points="697,493 960,493 960,549 599,549" fill="var(--wedge-grey)"/>
    </svg>

    <div class="brand brand--front">
      <span class="brand__dot"></span>
      <span class="brand__name">Brightcore Living</span>
    </div>

    <p class="tagline tagline--front">The journey home starts with you</p>
  </section>

</body>
</html>
```